Redesign of business card for Cedar Ridge Mechanical

We are looking for a new design for our business cards for Cedar Ridge Mechanical. We are a plumbing & HVAC construction company, operating on the West Coast of Canada and USA. Logo attached.
Industry/Entity Type
Construction - Plumbing & HVAC
Contact Information for Business Card
Name, address, phone numbers, email, website address
Look and feel
Each slider illustrates characteristics of the customer's brand and the style your logo design should communicate.

```html
<!DOCTYPE html>
<html lang="en">
<head>
<meta charset="utf-8">
<title>Cedar Ridge Mechanical – Business Card</title>
<link rel="stylesheet" href="https://fonts.googleapis.com/css2?family=Montserrat:wght@400;500;600;700&display=swap">
<style>
  :root {
    --canvas: #e9e6e2;
    --ink: #1c1c1c;
    --paper: #ffffff;
    --card-black: #161616;
    --mark-dark: #3a3a3a;
    --band: #232323;
    --band-text: #ffffff;
  }
  * { box-sizing: border-box; margin: 0; padding: 0; }
  html, body {
    width: 1200px; height: 900px; overflow: hidden;
    background: var(--canvas);
    font-family: "Montserrat", Arial, sans-serif;
    color: var(--ink);
  }
  .sheet {
    position: relative; width: 1200px; height: 900px;
    display: flex; flex-direction: column; align-items: center; justify-content: center; gap: 40px;
  }
  .card {
    position: relative; width: 700px; height: 400px; overflow: hidden;
    box-shadow: 0 6px 18px rgba(0,0,0,0.18);
  }
  /* Front */
  .card--front { background: var(--card-black); display: flex; align-items: center; justify-content: center; }
  .wordmark { display: flex; align-items: center; gap: 14px; font-weight: 700; letter-spacing: 2px; text-transform: uppercase; }
  .wordmark__square { width: 22px; height: 22px; background: currentColor; }
  .card--front .wordmark { color: var(--mark-dark); font-size: 30px; }
  /* Back */
  .card--back { background: var(--paper); }
  .card--back .wordmark { position: absolute; right: 50px; top: 100px; color: var(--ink); font-size: 20px; letter-spacing: 1.5px; }
  .card--back .wordmark__square { width: 16px; height: 16px; }
  .person { position: absolute; left: 50px; top: 150px; }
  .person__name { font-size: 27px; font-weight: 700; letter-spacing: 0.5px; }
  .person__title { font-size: 15px; font-weight: 500; margin-top: 2px; }
  .person__rule { width: 230px; height: 2px; background: var(--ink); margin: 6px 0 0 -10px; }
  .contacts { position: absolute; left: 44px; top: 232px; list-style: none; }
  .contacts li { display: flex; align-items: center; gap: 12px; font-size: 15px; height: 28px; }
  .contacts svg { width: 15px; height: 15px; fill: var(--ink); flex: none; }
  .divider { position: absolute; left: 390px; right: 50px; top: 300px; height: 2px; background: var(--ink); }
  .band { position: absolute; left: 0; bottom: 0; width: 700px; height: 44px; }
  .band__address { position: absolute; right: 30px; bottom: 11px; color: var(--band-text); font-size: 15px; font-weight: 500; letter-spacing: 0.3px; }
</style>
</head>
<body>
<main class="sheet">
  <section class="card card--front" aria-label="Card front">
    <div class="wordmark"><span class="wordmark__square"></span>Cedar Ridge Mechanical</div>
  </section>

  <section class="card card--back" aria-label="Card back">
    <div class="wordmark"><span class="wordmark__square"></span>Cedar Ridge Mechanical</div>

    <div class="person">
      <h1 class="person__name">Daniel Hart</h1>
      <p class="person__title">Managing Director</p>
      <div class="person__rule"></div>
    </div>

    <ul class="contacts">
      <li><svg viewBox="0 0 24 24"><path d="M6.6 10.8a15.1 15.1 0 0 0 6.6 6.6l2.2-2.2a1 1 0 0 1 1-.25 11.4 11.4 0 0 0 3.6.57 1 1 0 0 1 1 1V20a1 1 0 0 1-1 1A17 17 0 0 1 3 4a1 1 0 0 1 1-1h3.5a1 1 0 0 1 1 1c0 1.25.2 2.45.57 3.57a1 1 0 0 1-.25 1z"/></svg>555.204.7731</li>
      <li><svg viewBox="0 0 24 24"><path d="M2 5h20v14H2z M2 5l10 8 10-8" /></svg>info@cedarridgemechanical.com</li>
      <li><svg viewBox="0 0 24 24"><path d="M12 2a10 10 0 1 0 0 20 10 10 0 0 0 0-20zm0 2c1 1.3 1.8 3.4 2 6h-4c.2-2.6 1-4.7 2-6zM4.1 13h3.9c.1 2.2.6 4.2 1.4 5.6A8 8 0 0 1 4.1 13zm0-2a8 8 0 0 1 5.3-5.6C8.6 6.8 8.1 8.8 8 11zm7.9 9c-1-1.3-1.8-3.4-2-7h4c-.2 3.6-1 5.7-2 7zm2.6-1.4c.8-1.4 1.3-3.4 1.4-5.6h3.9a8 8 0 0 1-5.3 5.6zM16 11c-.1-2.2-.6-4.2-1.4-5.6A8 8 0 0 1 19.9 11z"/></svg>www.cedarridgemechanical.com</li>
    </ul>

    <div class="divider"></div>

    <svg class="band" viewBox="0 0 700 44" aria-hidden="true">
      <polygon points="0,30 260,30 250,44 0,44" fill="var(--band)"/>
      <polygon points="285,0 700,0 700,44 255,44" fill="var(--band)"/>
    </svg>
    <p class="band__address">240 Harbor View Road Salem, OR 97301</p>
  </section>
</main>
</body>
</html>
```